Modern Business Card

Modern professional business card with more than just logo and demographic info. Something memorable.

We are a trendy/modern chiropractic group with an emphasis on neurology, hence the minimalist-type brain logo. We want to convey that modern and technical aspect with professionalism and the elite nature of our practice environment.

```html
<!DOCTYPE html>
<html lang="en">
<head>
<meta charset="utf-8">
<title>Vertra Chiropractic – Business Card</title>
<link rel="stylesheet" href="https://fonts.googleapis.com/css2?family=Lora:wght@400;500&family=Signika:wght@600&family=Roboto:wght@400&display=swap">
<style>
  :root {
    --backdrop: #b9b9b9;
    --card: #f1f1f1;
    --brand-blue: #3b5c98;
    --brand-dark: #3d3235;
    --ink: #3a3a3a;
    --ink-soft: #4a4a4a;
    --white: #ffffff;
  }
  * { margin: 0; padding: 0; box-sizing: border-box; }
  html, body { width: 1200px; height: 576px; overflow: hidden; }
  body {
    background: var(--backdrop);
    position: relative;
    font-family: "Lora", Georgia, serif;
    color: var(--ink);
  }
  .card {
    position: absolute;
    top: 139px;
    width: 484px;
    height: 292px;
    background: var(--card);
    border-radius: 10px;
    overflow: hidden;
    box-shadow: 0 3px 8px rgba(0,0,0,0.25);
  }
  .card--front { left: 82px; }
  .card--back { left: 602px; }

  .brand {
    position: absolute;
    display: flex;
    align-items: center;
  }
  .brand__mark { background: var(--brand-blue); flex: none; }
  .brand__name {
    font-family: "Lora", Georgia, serif;
    font-weight: 400;
    color: var(--brand-dark);
    letter-spacing: 0.02em;
    line-height: 1.05;
  }
  .card--front .brand { left: 78px; top: 90px; gap: 20px; }
  .card--front .brand__mark { width: 64px; height: 64px; }
  .card--front .brand__name { font-size: 34px; }

  .card--back .brand { left: 30px; top: 110px; gap: 12px; }
  .card--back .brand__mark { width: 40px; height: 40px; }
  .card--back .brand__name { font-size: 21px; }

  .front__web {
    position: absolute;
    top: 246px;
    left: 0; right: 0;
    display: flex;
    justify-content: center;
    align-items: center;
    gap: 14px;
    font-family: "Roboto", Arial, sans-serif;
    font-size: 13px;
    color: #222;
  }
  .front__web svg { display: block; }
  .front__band {
    position: absolute;
    left: 0; right: 0; bottom: 0;
    height: 13px;
    display: flex;
  }
  .front__band span { flex: 1; }
  .front__band .blue { background: var(--brand-blue); }
  .front__band .dark { background: var(--brand-dark); }

  .person { position: absolute; left: 272px; top: 54px; }
  .person__name {
    font-family: "Signika", Arial, sans-serif;
    font-weight: 600;
    font-size: 20px;
    color: var(--brand-blue);
  }
  .person__title { font-size: 12.5px; color: var(--ink-soft); margin-top: 2px; }

  .contact {
    position: absolute;
    left: 272px; top: 118px;
    list-style: none;
    font-size: 12px;
    color: var(--ink-soft);
  }
  .contact li { display: flex; align-items: center; gap: 8px; height: 18.5px; }
  .contact svg { width: 12px; height: 12px; fill: var(--brand-blue); flex: none; }
  .address {
    position: absolute;
    left: 272px; top: 176px;
    font-style: normal;
    font-size: 12px;
    line-height: 18.5px;
    color: var(--ink-soft);
  }
  .back__band {
    position: absolute;
    left: 0; bottom: 0;
    width: 250px; height: 11px;
    background: var(--brand-dark);
  }
  .back__tab { position: absolute; left: 228px; bottom: 0; }
  .back__company {
    position: absolute;
    left: 272px; bottom: 11px;
    font-size: 12px;
    color: var(--white);
  }
</style>
</head>
<body>

  <section class="card card--front">
    <div class="brand">
      <span class="brand__mark"></span>
      <span class="brand__name">VERTRA<br>CHIROPRACTIC</span>
    </div>
    <div class="front__web">
      <svg width="46" height="4" viewBox="0 0 46 4"><polygon points="0,2 46,0 46,4" fill="var(--brand-blue)"/></svg>
      <span>www.vertrachiropractic.com</span>
      <svg width="46" height="4" viewBox="0 0 46 4"><polygon points="0,0 46,2 0,4" fill="var(--brand-blue)"/></svg>
    </div>
    <div class="front__band"><span class="blue"></span><span class="dark"></span></div>
  </section>

  <section class="card card--back">
    <div class="brand">
      <span class="brand__mark"></span>
      <span class="brand__name">VERTRA<br>CHIROPRACTIC</span>
    </div>

    <div class="person">
      <div class="person__name">Mark Lee Porter</div>
      <div class="person__title">Managing Director</div>
    </div>

    <ul class="contact">
      <li>
        <svg viewBox="0 0 12 12"><path d="M1 4 Q6 0 11 4 L9 5 L8 3.5 L4 3.5 L3 5 Z M3 6 L9 6 L10 11 L2 11 Z"/></svg>
        555-010-2020
      </li>
      <li>
        <svg viewBox="0 0 12 12"><path d="M1 3 H11 V10 H1 Z M1.8 3.8 L6 7 L10.2 3.8" stroke="var(--card)" stroke-width="0.9"/></svg>
        mark@vertrachiropractic.com
      </li>
      <li>
        <svg viewBox="0 0 12 12"><circle cx="6" cy="6" r="5"/><path d="M1 6 H11 M6 1 V11 M6 1 Q3 6 6 11 M6 1 Q9 6 6 11" stroke="var(--card)" stroke-width="0.7" fill="none"/></svg>
        www.vertrachiropractic.com
      </li>
    </ul>

    <address class="address">418 Harbor Lane, Westfield,<br>Lakeview, US 204517</address>

    <div class="back__band"></div>
    <svg class="back__tab" width="256" height="38" viewBox="0 0 256 38">
      <path d="M0 38 L14 6 Q17 0 24 0 L246 0 Q256 0 256 10 L256 38 Z" fill="var(--brand-blue)"/>
    </svg>
    <div class="back__company">Vertra Chiropractic LLC</div>
  </section>

</body>
</html>
```